Crale Electrical Solar Energy Marketing Flyer

Seeking a flyer to market our electrical business - promoting solar energy systems. Will be used as print marketing.

Attached are similar examples in the industry, as well as current Crale Electrical ads and our new "Crale Electrical, Air & Solar" logo.

We would like the reverse side to have information relating to solar for business.

This flyer is to promote the solar arm of our business, however we also deliver electrical and air-conditioning services. If possible it would be great to have a small reference to our air-conditioning service on the front page.We also need to reference the we have finance available.
Updates

Project Deadline Extended Reason: Apologies - due to illness I had been unable to complete the required text copy for flyer. Please note any slight changes to brief and copy will be updated urgently today while I am back in the office. There are some great flyers catching our eye. Added Monday, July 18, 2016

Target Market(s)

Home and Business Owners

Industry/Entity Type

Solar Energy

Logo Text

Crale Electrical, Air & Solar

Requirements
Must have
• Company logo, WPD installer logo, Lumivar Logo, phone number and all licences stated on the attached Crale Electrical ad. Catchy, uncomplicated appearance. Colours and pics to compliment logo. Disclaimer
Nice to have
• Testimonial

```html
<!DOCTYPE html>
<html lang="en">
<head>
<meta charset="utf-8">
<title>Crale Electrical – Invest in Solar Flyer</title>
<link href="https://fonts.googleapis.com/css2?family=Anton&family=Lato:wght@400;700;900&family=Roboto+Condensed:wght@700&display=swap" rel="stylesheet">
<style>
  :root{
    --backdrop:#e8e5e0;
    --paper:#ffffff;
    --red:#a3191f;
    --red-deep:#7e0f14;
    --blue:#1f86d1;
    --blue-deep:#1463b3;
    --ink:#1c1c1c;
    --tan:#d6a865;
    --orange:#f08a24;
    --grey:#c9ccd1;
  }
  *{box-sizing:border-box;margin:0;padding:0}
  html,body{width:888px;height:1200px;overflow:hidden;background:var(--backdrop)}
  .canvas{position:relative;width:888px;height:1200px}
  .flyer{position:absolute;left:78px;top:82px;width:732px;height:1036px;background:var(--paper);overflow:hidden;box-shadow:0 4px 14px rgba(0,0,0,.25)}
  .flyer > *{position:absolute}
  .hero-art{left:0;top:0;width:732px;height:1036px}
  .brand{left:18px;top:352px;display:flex;align-items:center;gap:8px;font-family:"Lato",sans-serif;font-weight:900;font-size:19px;color:#ffffff}
  .brand-dot{width:30px;height:30px;border-radius:50%;background:var(--red)}
  .finance-badge{left:287px;top:355px;width:160px;height:160px}
  .finance-text{left:287px;top:374px;width:160px;text-align:center;font-family:"Anton",sans-serif;font-size:27px;line-height:40px;color:#fff;letter-spacing:.5px}
  .headline-box{left:406px;top:530px;width:308px;height:176px;background:linear-gradient(#ffffff,#e4e6ea);border-radius:4px;box-shadow:0 6px 10px rgba(0,0,0,.25);text-align:center;font-family:"Anton",sans-serif;line-height:1}
  .headline-top{display:block;margin-top:10px;font-size:72px;color:var(--red)}
  .headline-main{display:block;margin-top:0;font-size:96px;color:var(--blue)}
  .tax-title{left:37px;top:572px;font-family:"Lato",sans-serif;font-weight:700;font-size:44px;color:var(--ink);letter-spacing:-.5px;white-space:nowrap}
  .tax-sub{left:37px;top:624px;font-family:"Lato",sans-serif;font-weight:700;font-size:32px;color:var(--blue);white-space:nowrap}
  .tax-body{left:37px;top:686px;font-family:"Lato",sans-serif;font-weight:700;font-size:15.5px;line-height:20px;color:var(--ink);white-space:nowrap}
  .disclaimer{left:37px;top:750px;font-family:"Lato",sans-serif;font-size:10.5px;line-height:13px;color:#333;white-space:nowrap}
  .services-band{left:0;top:802px;width:360px;height:70px;background:var(--tan);border-radius:0 14px 14px 0;padding:5px 0 0 37px;font-family:"Roboto Condensed",sans-serif;font-weight:700;font-size:24px;line-height:30px;color:var(--ink);white-space:nowrap}
  .services-band span{color:#fff}
  .phone{left:414px;top:745px;display:flex;align-items:center;gap:6px;font-family:"Lato",sans-serif;font-weight:700;font-size:41px;color:var(--ink);white-space:nowrap}
  .phone svg{width:26px;height:26px}
  .rule{height:2px;background:linear-gradient(90deg,transparent,var(--grey),transparent)}
  .rule-phone{left:420px;top:796px;width:290px}
  .rule-quote{left:420px;top:864px;width:290px}
  .quote{left:380px;top:808px;width:320px;text-align:right;font-family:"Roboto Condensed",sans-serif;font-weight:700;font-size:20px;line-height:25px;color:var(--ink)}
  .quote b{color:var(--blue)}
  .finance-partner{left:40px;top:888px;font-family:"Lato",sans-serif;text-align:center;width:210px}
  .partner-name{display:flex;align-items:center;justify-content:center;gap:8px;font-weight:400;font-size:30px;color:#444}
  .partner-square{width:22px;height:22px;background:var(--blue)}
  .partner-tag{display:block;margin-top:4px;font-size:14px;font-weight:700;color:var(--ink)}
  .licences{left:272px;top:906px;font-family:"Roboto Condensed",sans-serif;font-weight:700;font-size:16px;line-height:21px;color:var(--ink);white-space:nowrap}
  .installer-badge{left:496px;top:900px;width:200px;height:64px}
</style>
</head>
<body>
<div class="canvas">
  <div class="flyer">
    <svg class="hero-art" viewBox="0 0 732 1036">
      <defs>
        <linearGradient id="leftPhoto" x1="0" y1="0" x2="1" y2="1">
          <stop offset="0" stop-color="#7fa9d8"/>
          <stop offset=".5" stop-color="#2a4f9e"/>
          <stop offset="1" stop-color="#6f5a50"/>
        </linearGradient>
        <linearGradient id="rightPhoto" x1="0" y1="0" x2="1" y2="1">
          <stop offset="0" stop-color="#a9c7ea"/>
          <stop offset=".4" stop-color="#4f7a3a"/>
          <stop offset=".75" stop-color="#2d4f96"/>
          <stop offset="1" stop-color="#6e5549"/>
        </linearGradient>
      </defs>
      <path role="img" aria-label="Photo: installer with a cordless drill fixing rooftop solar panels" fill="url(#leftPhoto)" d="M0 0 H90 Q240 280 460 410 Q300 430 0 560 Z"/>
      <path role="img" aria-label="Photo: smiling installer in safety harness seated beside solar panels on a shingle roof, trees and sky behind" fill="url(#rightPhoto)" d="M90 0 H732 V480 Q600 440 460 410 Q240 280 90 0 Z"/>
      <path d="M90 0 Q240 280 460 410" fill="none" stroke="#fff" stroke-width="12"/>
      <path fill="#fff" d="M0 620 C150 520 320 440 470 412 C560 422 650 470 732 520 V1036 H0 Z"/>
      <path fill="var(--red)" d="M0 540 C150 460 300 418 440 402 L470 412 C320 440 150 520 0 622 Z"/>
      <path fill="none" stroke="var(--blue)" stroke-width="4" d="M0 532 C150 454 300 412 440 396"/>
      <path fill="var(--blue-deep)" d="M470 412 C560 418 650 450 732 462 V522 C650 478 560 426 470 412 Z"/>
      <path fill="var(--red)" d="M0 990 L20 982 L34 992 L52 978 L70 988 L92 976 L110 990 L132 980 L150 986 L172 974 L190 988 L214 978 L232 990 L256 976 L274 986 L298 980 L318 992 L340 976 L362 988 L384 978 L402 990 L426 980 L446 986 L468 974 L488 988 L510 978 L530 990 L552 976 L574 986 L596 980 L616 992 L640 978 L660 988 L684 976 L706 990 L732 980 V1036 H0 Z"/>
    </svg>

    <div class="brand"><span class="brand-dot"></span>Crale Electrical, Air &amp; Solar</div>

    <svg class="finance-badge" viewBox="0 0 160 160" aria-hidden="true">
      <circle cx="80" cy="80" r="72" fill="var(--red)" stroke="var(--red)" stroke-width="14" stroke-dasharray="6 5"/>
      <circle cx="80" cy="80" r="70" fill="none" stroke="var(--red-deep)" stroke-width="2"/>
    </svg>
    <div class="finance-text">WE HAVE<br>FINANCE<br>AVAILABLE</div>

    <div class="headline-box">
      <span class="headline-top">INVEST IN</span>
      <span class="headline-main">SOLAR!</span>
    </div>

    <h2 class="tax-title">$20,000 TAX =</h2>
    <p class="tax-sub">Break For Business!</p>
    <p class="tax-body">With business expenses up to $20,000 now<br>being 100% Tax Deductable* - Now is the time<br>to install solar energy for your small business!</p>
    <p class="disclaimer">*All customers advised to seek advice of registered accountant<br>to determine tax benefit and eligibility. Subject to change.</p>

    <p class="services-band">We also deliver electrical and<br><span>air-conditioning services</span></p>

    <p class="phone">
      <svg viewBox="0 0 24 24" aria-hidden="true"><path fill="var(--red)" d="M6.6 10.8a15.2 15.2 0 0 0 6.6 6.6l2.2-2.2a1 1 0 0 1 1-.25 11.4 11.4 0 0 0 3.6.57 1 1 0 0 1 1 1V20a1 1 0 0 1-1 1A17 17 0 0 1 3 4a1 1 0 0 1 1-1h3.5a1 1 0 0 1 1 1c0 1.25.2 2.45.57 3.57a1 1 0 0 1-.25 1z"/></svg>
      1300 555 019
    </p>
    <div class="rule rule-phone"></div>
    <p class="quote">For a <b>FREE</b> quote contact<br>a local Electrician you can trust!</p>
    <div class="rule rule-quote"></div>

    <div class="finance-partner">
      <span class="partner-name"><span class="partner-square"></span>Lumivar</span>
      <span class="partner-tag">NO INTEREST EVER!</span>
    </div>

    <p class="licences">Larkfield QLD 4521<br>Electrical Licence: 58231<br>WPD Accreditation: A0419876</p>

    <svg class="installer-badge" viewBox="0 0 200 64" role="img" aria-label="WPD accredited installer badge">
      <rect x="10" y="8" width="180" height="48" rx="6" fill="var(--orange)"/>
    </svg>
  </div>
</div>
</body>
</html>
```